Business Card Design

New business card design

Target Market(s)

Residential & Commercial Property Managers

Industry/Entity Type

Plumbing Services

Contact Information for Business Card

Name - Rowan Keddle, title - Director, Phone Number - 0431 286 517, email - rowan@tbk-plumbing.com.au, Company ABN - 73 215 904 386,

Font styles to use
Sans Serif

Colors
0054AA
0677BA
7BADD7
CADEEF
E8F1F8

```html
<!DOCTYPE html>
<html lang="en">
<head>
<meta charset="utf-8">
<title>Business Card – Front and Back</title>
<link rel="stylesheet" href="https://fonts.googleapis.com/css2?family=Poppins:wght@300;400;500;700&display=swap">
<style>
  :root {
    --backdrop: #222222;
    --card-white: #ffffff;
    --brand-blue: #29a8e0;
    --ink-navy: #1f2a33;
    --name-grey: #6b625a;
    --back-navy: #1c232b;
    --back-ink: #34414d;
    --white: #ffffff;
  }
  * { box-sizing: border-box; margin: 0; padding: 0; }
  html, body {
    width: 1200px; height: 780px; overflow: hidden;
    background: var(--backdrop);
    font-family: "Poppins", sans-serif;
  }
  .stage {
    position: relative; width: 1200px; height: 780px;
    display: flex; align-items: center; justify-content: center; gap: 50px;
  }
  .card {
    position: relative; width: 540px; height: 318px; overflow: hidden;
  }
  /* front */
  .card--front { background: var(--card-white); }
  .corner-tab {
    position: absolute; top: 0; right: 0; width: 30px; height: 16px;
    background: var(--brand-blue);
  }
  .name-block {
    position: absolute; top: 16px; right: 42px; text-align: right;
  }
  .name { font-size: 30px; line-height: 1.1; letter-spacing: 0.5px; }
  .name__first { color: var(--brand-blue); font-weight: 700; }
  .name__last { color: var(--name-grey); font-weight: 300; }
  .job-title { font-size: 13px; color: var(--ink-navy); font-weight: 400; margin-top: 2px; }
  .company-name {
    position: absolute; top: 104px; left: 40px;
    display: flex; align-items: center; gap: 12px;
    font-size: 30px; font-weight: 500; color: var(--ink-navy);
    letter-spacing: 0.5px;
  }
  .company-dot {
    width: 16px; height: 16px; border-radius: 50%; background: var(--brand-blue);
  }
  .abn {
    position: absolute; top: 186px; left: 40px;
    font-size: 15px; color: var(--brand-blue); font-weight: 400; letter-spacing: 0.5px;
  }
  .band { position: absolute; inset: 0; }
  .contact-list {
    position: absolute; top: 238px; left: 40px; list-style: none;
    color: var(--white); font-size: 14px; line-height: 24px; letter-spacing: 0.4px;
  }
  .contact-list li { display: flex; align-items: center; gap: 10px; }
  .contact-icon { width: 14px; height: 14px; flex: none; }
  /* back */
  .card--back { background: var(--back-navy); }
  .back-name {
    position: absolute; inset: 0; display: flex; align-items: center; justify-content: center; gap: 16px;
    font-size: 36px; font-weight: 500; color: var(--back-ink); letter-spacing: 1px;
  }
  .back-dot { width: 20px; height: 20px; border-radius: 50%; background: var(--brand-blue); }
</style>
</head>
<body>
<main class="stage">
  <section class="card card--front">
    <div class="corner-tab"></div>
    <div class="name-block">
      <p class="name"><span class="name__first">Rowan</span> <span class="name__last">Keddle</span></p>
      <p class="job-title">Director</p>
    </div>
    <div class="company-name"><span>tbk plumbing services</span><span class="company-dot"></span></div>
    <p class="abn">ABN – 73 215 904 386</p>
    <svg class="band" width="540" height="318" viewBox="0 0 540 318" aria-hidden="true">
      <polygon points="0,226 540,180 540,318 0,318" fill="var(--brand-blue)"/>
    </svg>
    <ul class="contact-list">
      <li>
        <svg class="contact-icon" viewBox="0 0 24 24"><path fill="#fff" d="M6.6 10.8a15.1 15.1 0 0 0 6.6 6.6l2.2-2.2c.3-.3.7-.4 1-.2 1.1.4 2.3.6 3.6.6.6 0 1 .4 1 1V20c0 .6-.4 1-1 1A17 17 0 0 1 3 4c0-.6.4-1 1-1h3.5c.6 0 1 .4 1 1 0 1.3.2 2.5.6 3.6.1.3 0 .7-.2 1z"/></svg>
        <span>0431 286 517</span>
      </li>
      <li>
        <svg class="contact-icon" viewBox="0 0 24 24"><rect x="2" y="5" width="20" height="14" rx="2" fill="none" stroke="#fff" stroke-width="2"/><path d="M2 7l10 7 10-7" fill="none" stroke="#fff" stroke-width="2"/></svg>
        <span>www.tbk-plumbing.com.au</span>
      </li>
      <li>
        <svg class="contact-icon" viewBox="0 0 24 24"><circle cx="12" cy="12" r="10" fill="none" stroke="#fff" stroke-width="2"/><path d="M2 12h20M12 2c3 3 3 17 0 20M12 2c-3 3-3 17 0 20" fill="none" stroke="#fff" stroke-width="1.6"/></svg>
        <span>rowan@tbk-plumbing.com.au</span>
      </li>
    </ul>
  </section>

  <section class="card card--back">
    <div class="back-name"><span>tbk plumbing services</span><span class="back-dot"></span></div>
  </section>
</main>
</body>
</html>
```